A comprehensive online math curriculum teaching service needs a Landing Page design

We need a Landing Page design for a startup company based in Edmonton, Alberta, Canada, called Brevanta Numérica. Brevanta Numérica is a comprehensive online math curriculum service for independently schooled students in grades 6-12 worldwide. Instruction is delivered through a one-on-one, virtual, adaptive classroom that uses integrated, interactive digital whiteboards for both teachers and students, with a standard modular lesson workflow for mastering math. Brevanta Numérica is designed to help students from all socioeconomic backgrounds master mathematics.

The landing Page should use the same colour scheme as our recently designed PowerPoint template (attached for reference: Design 36712224). Our logo is in the PowerPoint template. I also attached a draft wireframe of our landing page to guide the design.

Target Market(s)

Independently schooled students in grades 6 through 12 worldwide

Industry/Entity Type

Education - Mathematics teaching

Requirements
Must have
• Consistent colours with PowerPoint design

```html
<!DOCTYPE html>
<html lang="en">
<head>
<meta charset="utf-8">
<title>Brevanta Numérica — Online Math Curriculum</title>
<link href="https://fonts.googleapis.com/css2?family=Lato:wght@400;700;900&display=swap" rel="stylesheet">
<style>
:root{
  --blue:#2d5be3;
  --navy:#1b2550;
  --navy-dark:#141c3e;
  --ink:#1d1d1f;
  --text:#55585f;
  --muted:#7b7e86;
  --green:#1f4d3a;
  --green-light:#2f6b50;
  --footer:#0e1c16;
  --mist:#e9ebf2;
  --white:#ffffff;
}
*{margin:0;padding:0;box-sizing:border-box}
html,body{width:1200px;height:5168px;overflow:hidden}
body{font-family:"Lato",sans-serif;color:var(--text);background:var(--white);position:relative}
.abs{position:absolute}
.btn{position:absolute;display:flex;align-items:center;justify-content:center;color:var(--white);font-weight:700;font-size:15px;border-radius:3px}
.btn-blue{background:var(--blue)}
.btn-navy{background:var(--navy)}

/* header */
.brand{position:absolute;left:142px;top:30px;display:flex;align-items:center;gap:12px}
.brand-dot{width:34px;height:34px;border-radius:50%;background:var(--navy)}
.brand-name{font-size:28px;color:var(--ink);line-height:1}
.brand-tag{font-size:13px;color:var(--text);margin-top:8px}
.nav{position:absolute;left:540px;top:72px;display:flex;gap:28px;font-size:15px;color:var(--ink)}
.nav span:first-child{border-left:2px solid var(--ink);padding-left:10px}

/* hero */
.chalk{position:absolute;left:0;top:128px;width:1200px;height:340px;background:linear-gradient(180deg,#295a45,#1d4634)}
.hero-card{position:absolute;left:52px;top:296px;width:1096px;height:720px;background:var(--white);border-radius:140px 140px 0 0}
.hero-title{position:absolute;left:0;top:370px;width:1200px;text-align:center;font-size:42px;font-weight:700;color:var(--ink)}
.hero-copy{position:absolute;left:160px;top:474px;width:426px;font-size:15px;line-height:27px;text-align:justify}
.hero-art{position:absolute;left:668px;top:508px;width:390px;height:390px;border-radius:12px;background:radial-gradient(circle at 40% 45%,#dfe7f7,#f5f7fc 70%)}

/* proficiency */
.mist{position:absolute;left:-90px;top:1016px;width:1390px;height:940px;border-radius:50%;background:var(--mist)}
.prof-title{position:absolute;left:140px;top:1144px;font-size:44px;font-weight:700;color:var(--ink)}
.prof-lead{position:absolute;left:414px;top:1150px;font-size:18px;font-weight:700;color:var(--ink)}
.prof-sub{position:absolute;left:414px;top:1180px;font-size:15px;color:var(--text)}
.need h4{font-size:15px;font-weight:700;color:var(--navy);margin-bottom:4px}
.need p{font-size:14px;line-height:20px;color:var(--text)}
.need.r{text-align:right}
.need.j p{text-align:justify}

/* how it works */
.section-title{position:absolute;left:0;width:1200px;text-align:center;font-size:42px;font-weight:700;color:var(--ink)}
.how-sub{position:absolute;left:0;top:2156px;width:1200px;text-align:center;font-size:17px;line-height:27px}
.tab{position:absolute;left:146px;width:240px;height:38px;display:flex;align-items:center;justify-content:center;color:var(--white);font-size:15px;border-radius:3px}
.feature{position:absolute;left:472px;width:586px}
.feature-head{display:flex;align-items:center;gap:14px;font-size:19px;color:var(--ink)}
.feature-icon{width:46px;height:46px;border-radius:50%;background:var(--blue);display:flex;align-items:center;justify-content:center}
.feature p{margin:18px 0 0 60px;font-size:14px;line-height:27px}
.learn{position:absolute;left:532px;top:2604px;font-size:17px;color:var(--blue);font-weight:700;display:flex;align-items:center;gap:10px}

/* lessons */
.board{position:absolute;left:0;top:2700px;width:1200px;height:300px;background:linear-gradient(180deg,#2a5c46,#1c4533)}
.lesson-title{position:absolute;left:0;top:2778px;width:1200px;text-align:center;font-size:44px;font-weight:700;color:var(--white)}
.card{position:absolute;top:2888px;width:448px;height:1008px;background:var(--white);border-radius:8px;box-shadow:0 6px 24px rgba(20,28,62,.14)}
.card-title{position:absolute;left:0;top:50px;width:100%;text-align:center;font-size:19px;line-height:28px;color:var(--ink)}
.step{position:absolute;left:28px;width:392px}
.step-num{position:absolute;left:0;top:0;width:28px;height:28px;border-radius:50%;background:var(--navy);color:var(--white);font-size:11px;font-weight:700;display:flex;align-items:center;justify-content:center}
.step-num.blue{background:var(--blue)}
.step-name{position:absolute;left:48px;top:4px;font-size:17px;color:var(--ink)}
.step-time{position:absolute;right:0;top:4px;font-size:13px;color:var(--muted)}
.step-desc{position:absolute;left:50px;top:36px;width:260px;font-size:14px;line-height:20px}
.sub{position:absolute;left:120px;width:290px}
.sub-name{font-size:14px;color:var(--ink)}
.sub-time{position:absolute;right:10px;top:0;font-size:11px;color:var(--muted)}
.sub p{font-size:11px;line-height:17px;margin-top:12px;width:210px}
.rail{position:absolute;left:41px;border-left:2px dotted #b9bed0}

/* about */
.about-title{position:absolute;left:146px;top:4012px;font-size:42px;font-weight:700;color:var(--ink)}
.about-copy{position:absolute;left:146px;top:4076px;width:426px;font-size:15px;line-height:27px;text-align:justify}
.about-photo{position:absolute;left:634px;top:3998px;width:566px;height:454px;border-radius:260px 0 0 220px;background:linear-gradient(120deg,#c9b39b,#8d6f55 55%,#4f5a66)}

/* footer */
.footer-shape{position:absolute;left:0;top:4520px}
.foot-brand{position:absolute;left:0;top:4656px;width:1200px;display:flex;justify-content:center;align-items:center;gap:14px;color:var(--white)}
.foot-brand .brand-dot{background:var(--white)}
.foot-name{font-size:34px;line-height:1}
.foot-tag{position:absolute;left:0;top:4718px;width:1200px;text-align:center;font-size:15px;color:#d8dfdb;padding-left:40px}
.foot-nav{position:absolute;left:0;top:4786px;width:1200px;display:flex;justify-content:center;gap:32px;font-size:15px;color:var(--white)}
.contacts{position:absolute;left:0;top:4844px;width:1200px;display:flex;justify-content:center;gap:56px;font-size:20px;color:var(--white)}
.contacts span{display:flex;align-items:center;gap:14px}
.c-icon{width:28px;height:28px;border-radius:50%;background:var(--white)}
.legal{position:absolute;left:0;top:4980px;width:1200px;text-align:center;font-size:13px;color:var(--white)}
.social{position:absolute;left:0;top:5034px;width:1200px;display:flex;justify-content:center;gap:10px}
.social span{width:42px;height:42px;border-radius:50%;border:2px solid var(--white)}
</style>
</head>
<body>

<!-- header -->
<header>
  <div class="brand">
    <div class="brand-dot"></div>
    <div>
      <div class="brand-name">Brevanta Numérica</div>
      <div class="brand-tag">Inspiring Math · Empowering Learning</div>
    </div>
  </div>
  <div class="btn btn-blue" style="left:584px;top:0;width:234px;height:34px">Register a Student</div>
  <div class="btn btn-navy" style="left:824px;top:0;width:230px;height:34px">Free Consultation</div>
  <nav class="nav"><span>Home</span><span>Features</span><span>Program</span><span>Tuition</span><span>About Us</span><span>Contact Us</span></nav>
</header>

<!-- hero -->
<div class="chalk" role="img" aria-label="Green chalkboard with hand-drawn math doodles"></div>
<div class="hero-card"></div>
<h1 class="hero-title">Brevanta Numérica</h1>
<p class="hero-copy">Accelerated educational outcome is a comprehensive online math curriculum teaching service for independently schooled students in grades 6 through 12 worldwide. Teaching is done through our math academy, a one-on-one, virtual adaptive classroom that uses integrated, interactive digital whiteboards for both teachers and students. Brevanta Math Academy will open its virtual doors for the first cohort of grade 6 students in September 2026.Registration for Term One math classes opens on June 1, 2026 and closes in the middle of August 2026.Brevanta Numérica is designed to help students from all socioeconomic backgrounds master mathematics. We teach comprehensive grade 6-12 math curricula to independently schooled students.</p>
<div class="btn btn-blue" style="left:160px;top:880px;width:192px;height:40px">Register a Student</div>
<div class="btn btn-navy" style="left:362px;top:880px;width:192px;height:40px">Free Consultation</div>
<div class="hero-art" role="img" aria-label="Illustration of a teacher at a whiteboard connected to three students at computers"></div>

<!-- proficiency -->
<div class="mist"></div>
<h2 class="prof-title">Proficiency</h2>
<div class="prof-lead">Making math education engaging, effective, and within everyone's reach.</div>
<div class="prof-sub">Teaching math to independently schooled students is not easy. We know the challenges:</div>

<svg class="abs" style="left:400px;top:1330px" width="440" height="440" viewBox="0 0 440 440">
  <circle cx="220" cy="220" r="152" fill="none" stroke="var(--navy)" stroke-width="118"/>
  <g stroke="var(--mist)" stroke-width="14">
    <line x1="220" y1="220" x2="-10" y2="87"/>
    <line x1="220" y1="220" x2="220" y2="-10"/>
    <line x1="220" y1="220" x2="450" y2="87"/>
    <line x1="220" y1="220" x2="450" y2="353"/>
    <line x1="220" y1="220" x2="220" y2="450"/>
    <line x1="220" y1="220" x2="-10" y2="353"/>
  </g>
  <circle cx="220" cy="220" r="90" fill="var(--white)"/>
  <circle cx="220" cy="220" r="78" fill="none" stroke="var(--navy)" stroke-width="4"/>
  <text x="220" y="214" text-anchor="middle" font-family="Lato, sans-serif" font-size="17" fill="var(--navy)">Brevanta</text>
  <text x="220" y="236" text-anchor="middle" font-family="Lato, sans-serif" font-size="17" fill="var(--navy)">Numérica</text>
  <g fill="none" stroke="var(--white)" stroke-width="2" stroke-linecap="round" stroke-linejoin="round">
    <!-- people -->
    <g transform="translate(144,88)"><circle cx="0" cy="-6" r="6"/><circle cx="-13" cy="-2" r="4"/><circle cx="13" cy="-2" r="4"/><path d="M-10 12a10 10 0 0 1 20 0zM-22 10a8 8 0 0 1 10-7M22 10a8 8 0 0 0-10-7"/></g>
    <!-- monitor -->
    <g transform="translate(296,88)"><rect x="-16" y="-12" width="32" height="20" rx="2"/><path d="M-6 14h12M0 8v6"/></g>
    <!-- star -->
    <g transform="translate(372,220)"><path d="M0-16l5 10 11 2-8 8 2 11-10-5-10 5 2-11-8-8 11-2z"/></g>
    <!-- smile -->
    <g transform="translate(296,352)"><circle r="16"/><circle cx="-5" cy="-4" r="1.5"/><circle cx="5" cy="-4" r="1.5"/><path d="M-7 5a8 8 0 0 0 14 0"/></g>
    <!-- book -->
    <g transform="translate(144,352)"><rect x="-12" y="-16" width="24" height="32" rx="2"/><path d="M-6-8h12M-6-2h12M-12 10h24"/></g>
    <!-- student -->
    <g transform="translate(68,220)"><circle cy="-12" r="5"/><path d="M-8 16V2a8 8 0 0 1 16 0v14M-8 6h-4M8 6h4"/></g>
  </g>
</svg>

<div class="abs need r" style="left:228px;top:1304px;width:230px"><h4>Limited subject expertise</h4><p>Struggling with advanced topics, forgotten knowledge, and specialized methods.</p></div>
<div class="abs need j" style="left:784px;top:1304px;width:272px"><h4>Ensuring conceptual understanding</h4><p>Over-reliance on procedures. Bridging the "why" of math and real-world applications.</p></div>
<div class="abs need r" style="left:130px;top:1472px;width:252px"><h4>Preparing for advanced math</h4><p>Am I preparing my child for advanced math and for successfully transitioning into higher education, skilled jobs, or entrepreneurship?</p></div>
<div class="abs need j" style="left:862px;top:1472px;width:196px"><h4>Assessment and feedback</h4><p>Am I using the proper evaluation process to assess my child's progress and identify their weaknesses? Am I providing timely feedback to my child?</p></div>
<div class="abs need r" style="left:170px;top:1720px;width:310px"><h4>Curriculum challenges</h4><p>How can I choose the right curriculum and supplementary materials? Can I successfully adapt pre-made plans?</p></div>
<div class="abs need j" style="left:732px;top:1742px;width:276px"><h4>Keeping math fun and engaging</h4><p>Creativity struggles, gamification challenges and overcoming math fatigue.</p></div>

<!-- how it works -->
<h2 class="section-title" style="top:2078px">How Brevanta Numérica Works</h2>
<p class="how-sub">Teaching comprehensive math curricula to independently schooled students in grades<br>6-12 through secure virtual classrooms.</p>
<div class="tab btn-blue" style="top:2294px">Pedagogical Methodology</div>
<div class="tab btn-navy" style="top:2348px">Virtual Classroom</div>

<div class="feature" style="top:2286px">
  <div class="feature-head"><span class="feature-icon"><svg width="20" height="20" viewBox="0 0 20 20"><path d="M3 17l1-5 9-9 4 4-9 9z" fill="var(--white)"/></svg></span>Effective Curriculum</div>
  <p>Time-tested and proven pedagogical methodology with three pillars:(1) new math concepts built on previously taught ones; (2) daily review of earlier math concepts to increase understanding; and (3) frequent, cumulative assessments to ensure students master each math skill as new ones are added.</p>
</div>
<div class="feature" style="top:2472px">
  <div class="feature-head"><span class="feature-icon"><svg width="20" height="20" viewBox="0 0 20 20"><rect x="4" y="2" width="12" height="16" rx="2" fill="var(--white)"/><path d="M7 6h6M7 9h6" stroke="var(--blue)" stroke-width="1.5"/></svg></span>Innovative Lesson Design</div>
  <p>Standard, modular 1 ½ hour lesson workflows designed to accelerate students' mastery of math skills and concepts.</p>
</div>
<div class="learn">Learn more <svg width="24" height="24" viewBox="0 0 24 24"><circle cx="12" cy="12" r="10" fill="none" stroke="var(--blue)" stroke-width="1.5"/><path d="M10 7l5 5-5 5" fill="none" stroke="var(--blue)" stroke-width="1.5"/></svg></div>

<!-- lesson design -->
<div class="board" role="img" aria-label="Green chalkboard background with faint math doodles"></div>
<h2 class="lesson-title">Innovative Lesson Design</h2>

<section class="card" style="left:144px">
  <div class="card-title">1 and 2 Hour Session Lesson WorkfloW<br>Grades 6 to 8</div>
  <div class="rail" style="top:186px;height:498px"></div>
  <div class="rail" style="top:700px;height:94px"></div>
  <div class="rail" style="top:808px;height:84px"></div>
  <div class="step" style="top:158px"><div class="step-num blue">01</div><div class="step-name">PREPARATION</div><div class="step-time">15 Minutes</div><div class="step-desc">Promotes mental math and problem-solving and setting the tone for the day's teaching session.</div></div>
  <div class="sub" style="top:296px"><div class="sub-name">Facts Practices</div><div class="sub-time">6 minutes timed event</div><p>Students practice to recall immediately or quickly calculate simple math facts Timed event to promote the fast recall of basic facts.</p></div>
  <div class="sub" style="top:422px"><div class="sub-name">Mental Math</div><div class="sub-time">6 minutes timed event</div><p>Students listen to problem and perform calculation mentally and write the answer. Timed event to promote agility</p></div>
  <div class="sub" style="top:544px"><div class="sub-name">Problem Solving</div><div class="sub-time">6 minutes timed event</div><p>Students practice critical-thinking skills daily.</p></div>
  <div class="step" style="top:644px"><div class="step-num">02</div><div class="step-name">NEW CONCEPTS</div><div class="step-time">15 Minutes</div><div class="step-desc">Introduces new math concepts in small increments.</div></div>
  <div class="step" style="top:744px"><div class="step-num">03</div><div class="step-name">LESSON PRACTICE</div><div class="step-time">15 Minutes</div><div class="step-desc">Opportunity for students to practice skills of new math concepts</div></div>
  <div class="step" style="top:852px"><div class="step-num">04</div><div class="step-name">HOMEWORK</div><div class="step-time">15 Minutes</div><div class="step-desc">Twenty-five to thirty problems to provide students with distributed practice that promote long-term retention of math concepts.</div></div>
</section>

<section class="card" style="left:608px">
  <div class="card-title">1 and 12 Hour Session Lesson Workflow<br>Grades 9 to 12</div>
  <div class="rail" style="top:186px;height:78px"></div>
  <div class="rail" style="top:294px;height:70px"></div>
  <div class="step" style="top:158px"><div class="step-num blue">01</div><div class="step-name">NEW CONCEPTS</div><div class="step-time">25 Minutes</div><div class="step-desc">Introduces new math concepts in small increments.</div></div>
  <div class="step" style="top:266px"><div class="step-num">02</div><div class="step-name">LESSON PRACTICE</div><div class="step-time">20 minutes</div><div class="step-desc">Opportunity for students to practice skills of new math concepts.</div></div>
  <div class="step" style="top:366px"><div class="step-num blue">03</div><div class="step-name">HOMEWORK</div><div class="step-time">45 minutes</div><div class="step-desc">Twenty-five to thirty problems to provide students with distributed practice that promote long-term retention of math concepts.</div></div>
  <div class="abs" style="left:344px;top:514px;font-size:13px;line-height:20px">1 hour and<br>30 minutes<br>per session</div>
</section>

<!-- about -->
<h2 class="about-title">About Us</h2>
<p class="about-copy">Our vision with Brevanta Numérica is to create a world where all children, regardless of background or community, have equal opportunity to excel in mathematics in middle and high school. We believe that mastery of mathematics is the key to success in middle school and high school, and our approach is designed to make this mastery accessible to all. We want to inspire every student to reach their full potential in math, regardless of their starting point, and we invite you to join us in this mission.Brevanta Numérica is a comprehensive online math curriculum teaching service for students in grades 6 through 12 worldwide.</p>
<div class="btn btn-blue" style="left:146px;top:4462px;width:138px;height:40px">Read More</div>
<div class="about-photo" role="img" aria-label="Photo of a student studying at a desk with books"></div>

<!-- footer -->
<svg class="footer-shape" width="1200" height="648" viewBox="0 0 1200 648" aria-hidden="true">
  <path d="M0 80C180 10 420 0 620 0S1020 40 1200 120V648H0Z" fill="var(--footer)"/>
</svg>
<div class="foot-brand"><div class="brand-dot"></div><div class="foot-name">Brevanta Numérica</div></div>
<div class="foot-tag">Inspiring Math · Empowering Learning</div>
<nav class="foot-nav"><span>FEATURES</span><span>/</span><span>PROGRAM</span><span>/</span><span>TUITION</span><span>/</span><span>ABOUT US</span><span>/</span><span>CONTACT US</span></nav>
<div class="contacts">
  <span><i class="c-icon"></i>hello@brevantanumerica.com</span>
  <span><i class="c-icon"></i>www.brevantanumerica.com</span>
</div>
<p class="legal">© 2026 Companyname.All rights reserved &nbsp;|&nbsp; Privacy Policy &nbsp;|&nbsp; Terms of use</p>
<div class="social" aria-label="Social links"><span></span><span></span><span></span></div>

</body>
</html>
```